KR Appraisals website redesign

I would like to refresh my existing website of www.krappraisals-example.com with new graphics, look and feel, as well as updated structure and wording. Content and layout changes have been uploaded to this project Brief.

My existing website has a dark feel. I am now looking for a light and energetic feel. Financial Services is my industry, so the website should be reflect that. I would also like to reflect the concepts of Trust, Service and Expertise.

The website must be serious and upmarket.

Target Market(s)

Corporate board members, CFO's, treasurers and controllers
Auditors, tax advisors, private equity and venture capital asset managers, investors, tax authorities

Industry/Entity Type

Financial Service

Coding

Coded - Design and coding required

Number of Pages Required

5+ page

Font styles to use
Sans Serif
Other font styles liked:
• Designer can choose another modern font

Colors
0355a3
3277b5
85acd3
eaf1f7
f37122
f68d4d
9bcb3c
acd037
cadf82

Requirements
Must have
• Good hi resolution pictures that convey "Finance", "Trust", "Service" or "Expertise".
• An anti-bot (such as Captcha) mechanism in the contact form.
Should not have
• Must not have all content on one rolling screen.

```html
<!DOCTYPE html>
<html lang="en">
<head>
<meta charset="utf-8">
<title>Services – KR Appraisals</title>
<link rel="stylesheet" href="https://fonts.googleapis.com/css2?family=Figtree:wght@500;600;700&family=Nunito+Sans:wght@300;400&display=swap">
<style>
  :root{
    --blue:#0355a3;
    --orange:#f37122;
    --green:#9bcb3c;
    --nav-grey:#6f6f6f;
    --text-grey:#666;
    --panel:#f2f2f2;
    --footer:#333333;
    --footer-line:#5a5a5a;
    --footer-text:#9a9a9a;
    --badge:#4a4a4a;
    --white:#ffffff;
  }
  *{margin:0;padding:0;box-sizing:border-box}
  html,body{width:1200px;height:1084px;overflow:hidden;background:var(--white)}
  body{position:relative;font-family:"Nunito Sans",sans-serif}

  .site-header{position:absolute;left:0;top:0;width:1200px;height:100px;
    background:linear-gradient(90deg,#dcdcd0 0%,#e9e9dc 30%,#eff0e2 65%,#f6f7e6 100%)}
  .brand{position:absolute;left:161px;top:34px;display:flex;align-items:center;gap:10px;
    font-family:"Figtree",sans-serif;font-weight:600;font-size:24px;color:#8a8a8a;letter-spacing:.5px}
  .brand-square{width:14px;height:14px;background:#8a8a8a}
  .main-nav{position:absolute;top:45px;left:0;width:1200px;font-family:"Figtree",sans-serif;
    font-weight:600;font-size:11.5px;color:var(--nav-grey);text-transform:uppercase}
  .main-nav a{position:absolute;color:inherit;text-decoration:none;white-space:nowrap}
  .main-nav a.active{color:var(--blue)}

  .page-title{position:absolute;left:0;top:186px;width:1200px;text-align:center;
    font-family:"Figtree",sans-serif;font-weight:700;font-size:38px;color:var(--orange);letter-spacing:-.3px}

  .service-panel{position:absolute;left:562px;top:274px;width:477px;height:367px;background:var(--panel)}
  .service-photo{position:absolute;left:161px;top:311px;width:439px;height:293px;
    background:radial-gradient(ellipse at 45% 50%,#9aa3ad 0%,#c9cdd2 45%,#e6e7e8 100%)}
  .service-heading{position:absolute;left:646px;top:395px;font-family:"Figtree",sans-serif;
    font-weight:700;font-size:31px;color:var(--green);white-space:nowrap}
  .service-text{position:absolute;left:646px;top:443px;width:350px;font-size:10.6px;
    line-height:18.8px;color:var(--text-grey);font-weight:400}

  .site-footer{position:absolute;left:0;top:731px;width:1200px;height:353px}
  .footer-shape{position:absolute;left:0;top:0}
  .footer-brand{position:absolute;left:0;top:60px;width:1200px;display:flex;justify-content:center;
    align-items:center;gap:10px;font-family:"Figtree",sans-serif;font-weight:600;font-size:24px;color:#8a8a8a}
  .footer-nav{position:absolute;left:161px;top:145px;width:879px;height:45px;
    border-top:1px solid var(--footer-line);border-bottom:1px solid var(--footer-line);
    font-family:"Figtree",sans-serif;font-weight:600;font-size:11.5px;color:var(--footer-text);text-transform:uppercase}
  .footer-nav a{position:absolute;top:15px;color:inherit;text-decoration:none;white-space:nowrap}
  .footer-nav a.active{color:var(--green)}
  .footer-col h3{position:absolute;font-family:"Figtree",sans-serif;font-weight:700;font-size:13.5px;color:var(--orange)}
  .footer-line{position:absolute;font-size:10.8px;color:var(--footer-text);white-space:nowrap}
  .footer-line .hl{color:var(--green)}
  .footer-line .wh{color:#e8e8e8}
  .contact-icon{position:absolute}
  .partner-badge{position:absolute;background:var(--badge);border-radius:4px}
</style>
</head>
<body>
  <header class="site-header">
    <div class="brand"><span class="brand-square"></span>KR Appraisals</div>
    <nav class="main-nav">
      <a style="left:611px">Home</a>
      <a style="left:686px">About</a>
      <a class="active" style="left:766px">Services</a>
      <a style="left:861px">News &amp; Views</a>
      <a style="left:985px">Contact</a>
    </nav>
  </header>

  <h1 class="page-title">OUR SERVICES</h1>

  <section class="service">
    <div class="service-panel"></div>
    <div class="service-photo" role="img" aria-label="Letter dice spelling risk and profit terms on a financial newspaper page"></div>
    <h2 class="service-heading">BUSINESS VALUATION</h2>
    <p class="service-text">Company stakeholders trust KR Appraisals to provide business valuations for transaction, accounting, tax, legal, and share or option participation purposes. Through our bespoke approach and global network, we customize teams to the needs of our clients.</p>
  </section>

  <footer class="site-footer">
    <svg class="footer-shape" width="1200" height="353" viewBox="0 0 1200 353">
      <polygon points="0,68 600,0 1200,68 1200,353 0,353" fill="#333333"/>
    </svg>
    <div class="footer-brand"><span class="brand-square"></span>KR Appraisals</div>
    <nav class="footer-nav">
      <a class="active" style="left:225px">Home</a>
      <a style="left:300px">About</a>
      <a style="left:380px">Services</a>
      <a style="left:475px">News &amp; Views</a>
      <a style="left:599px">Contact</a>
    </nav>

    <div class="footer-col">
      <h3 style="left:163px;top:216px">CREDITS</h3>
      <p class="footer-line" style="left:163px;top:246px">© 2019 <span class="hl">KR Appraisals B.V.</span></p>
      <p class="footer-line" style="left:163px;top:268px">Logo by <span class="wh">Mara Lindqvist</span></p>
      <p class="footer-line" style="left:163px;top:291px">Website by <span class="hl">Northgate Webworks</span></p>
    </div>

    <div class="footer-col">
      <h3 style="left:466px;top:216px">LEIDEN</h3>
      <svg class="contact-icon" style="left:467px;top:247px" width="10" height="14" viewBox="0 0 10 14">
        <path d="M5 0a5 5 0 0 0-5 5c0 3.6 5 9 5 9s5-5.4 5-9a5 5 0 0 0-5-5zm0 7a2 2 0 1 1 0-4 2 2 0 0 1 0 4z" fill="#9bcb3c"/>
      </svg>
      <p class="footer-line" style="left:485px;top:246px">Stationsweg 48</p>
      <p class="footer-line" style="left:485px;top:262px">2312 AV Leiden</p>
      <svg class="contact-icon" style="left:465px;top:294px" width="13" height="13" viewBox="0 0 24 24">
        <path d="M6.6 10.8a15.1 15.1 0 0 0 6.6 6.6l2.2-2.2a1 1 0 0 1 1-.25 11.4 11.4 0 0 0 3.6.57 1 1 0 0 1 1 1V20a1 1 0 0 1-1 1A17 17 0 0 1 3 4a1 1 0 0 1 1-1h3.5a1 1 0 0 1 1 1c0 1.25.2 2.45.57 3.6a1 1 0 0 1-.25 1z" fill="#9bcb3c"/>
      </svg>
      <p class="footer-line" style="left:485px;top:292px;color:#e8e8e8;font-size:11.5px">070 555 0142</p>
    </div>

    <div class="partner-badge" style="left:769px;top:258px;width:120px;height:28px" role="img" aria-label="Partner membership badge"></div>
    <div class="partner-badge" style="left:913px;top:244px;width:122px;height:50px" role="img" aria-label="Partner membership badge"></div>
  </footer>
</body>
</html>
```